Business card design for new eCommerce site focusing on integrity and strong businsess tactics

We need a business card that will stand out and be memorable. Something with color that matches our company logo colors. Think high end version of Pactivo. There are 2 logos provided. The parent company is called Amber Ledge Partners and we are presenting a new and very exciting eCommerce site called BrightHarborTrade.example.

Target Market(s)

Our target markets are in the Activities, Food and Beverage, Health and Beauty

Industry/Entity Type

Marketing

Contact Information for Business Card

We have 4 members that need cards...I will provide all info to the winner of the design contest
Business Address is
4870 West 63rd Avenue, Suite C207
Phoenix AZ 85731

Font styles to use
Serif
Sans Serif

Colors

Designer to choose colors to be used in the design.

Requirements
Must have
• The card must be memorable...should be unique in design but must exude integrity and be playful .
• I have provided several colors or our parent company...please feel free to use which ever
Nice to have
• I will leave this up to you. Feel free to use other images of your choosing that wraps around our client.....Activities, Dining, Health, Beauty
Should not have
• just dont be boring

```html
<!DOCTYPE html>
<html lang="en">
<head>
<meta charset="utf-8">
<title>BrightHarborTrade.example — Business Card</title>
<link rel="stylesheet" href="https://fonts.googleapis.com/css2?family=Open+Sans:wght@400;600&family=Quicksand:wght@500;700&display=swap">
<style>
  :root {
    --backdrop: #2e2925;
    --card: #0d0d0d;
    --ink-white: #f2f2f2;
    --brand-blue: #2d8fd0;
    --brand-green: #7cc242;
    --brand-teal: #2fb3a8;
    --tag-grey: #8a8a8a;
    --divider: #3f4a1f;
  }
  * { margin: 0; padding: 0; box-sizing: border-box; }
  html, body {
    width: 1200px; height: 900px; overflow: hidden;
    background: var(--backdrop);
  }
  .canvas {
    position: relative; width: 1200px; height: 900px;
    display: flex; align-items: center; justify-content: center; gap: 40px;
  }
  .card {
    position: relative; width: 540px; height: 310px;
    background: var(--card);
    border-radius: 4px;
    box-shadow: 0 14px 30px rgba(0,0,0,.45);
    overflow: hidden;
  }

  /* Front */
  .card-front .brand-mark {
    position: absolute; left: 34px; top: 135px;
    display: flex; align-items: center; gap: 8px;
  }
  .brand-dot {
    width: 16px; height: 16px; border-radius: 50%;
    background: var(--brand-blue); flex: none;
  }
  .brand-name {
    font-family: "Quicksand", sans-serif; font-weight: 700;
    font-size: 20px; color: var(--brand-green); letter-spacing: .2px;
  }
  .card-front .divider {
    position: absolute; left: 262px; top: 70px;
    width: 1px; height: 170px; background: var(--divider);
  }
  .contact {
    position: absolute; left: 284px; top: 64px;
    font-family: "Open Sans", sans-serif; color: var(--ink-white);
  }
  .contact-name {
    font-size: 17px; font-weight: 600; color: var(--brand-blue);
    text-transform: uppercase; letter-spacing: .3px; line-height: 1.1;
  }
  .contact-role { font-size: 13px; margin-bottom: 16px; }
  .contact-lines { list-style: none; font-size: 13px; line-height: 1.45; }
  .contact-lines li { display: flex; align-items: center; gap: 8px; }
  .contact-lines svg { width: 10px; height: 10px; fill: var(--brand-blue); flex: none; }
  .contact-address { margin-top: 12px; font-size: 13px; line-height: 1.4; }

  /* Back */
  .card-back {
    display: flex; flex-direction: column; align-items: center; justify-content: center;
  }
  .parent-name {
    font-family: "Quicksand", sans-serif; font-weight: 700;
    font-size: 22px; color: var(--brand-teal); margin-bottom: 46px;
  }
  .back-brand { display: flex; align-items: center; gap: 10px; }
  .back-brand .brand-dot { width: 20px; height: 20px; }
  .back-brand .brand-name { font-size: 24px; }
  .tagline {
    margin-top: 4px; margin-left: 30px;
    font-family: "Quicksand", sans-serif; font-weight: 500;
    font-size: 13px; color: var(--tag-grey); letter-spacing: .3px;
  }
</style>
</head>
<body>
<main class="canvas">

  <section class="card card-front" aria-label="Business card front">
    <div class="brand-mark">
      <span class="brand-dot"></span>
      <span class="brand-name">BrightHarborTrade</span>
    </div>
    <div class="divider"></div>
    <div class="contact">
      <p class="contact-name">Daniel Reyes</p>
      <p class="contact-role">Managing Director</p>
      <ul class="contact-lines">
        <li><svg viewBox="0 0 10 10"><path d="M2 0.5 L3.6 2.6 L2.8 3.6 C3.4 5 4.9 6.5 6.4 7.2 L7.4 6.4 L9.5 8 L8.4 9.5 C4.5 9 1 5.5 0.5 1.6 Z"/></svg>(044)555018274</li>
        <li><svg viewBox="0 0 10 10"><path d="M0 2 H10 V8 H0 Z M0.6 2.4 L5 5.6 L9.4 2.4 V2.9 L5 6.2 L0.6 2.9 Z" fill-rule="evenodd"/></svg>info@brightharbortrade.example</li>
        <li><svg viewBox="0 0 10 10"><circle cx="5" cy="5" r="4.6"/></svg>www.brightharbortrade.example</li>
      </ul>
      <p class="contact-address">4870 West 63rd Avenue,<br>Suite C207 Phoenix AZ 85731</p>
    </div>
  </section>

  <section class="card card-back" aria-label="Business card back">
    <p class="parent-name">Amber Ledge Partners</p>
    <div class="back-brand">
      <span class="brand-dot"></span>
      <span class="brand-name">BrightHarborTrade.example</span>
    </div>
    <p class="tagline">Activities-Dining-Health-Beauty</p>
  </section>

</main>
</body>
</html>
```